Need Flyer for Our Real estate Agency

Need to run General Campaign for our agency with Start of New Year as our theme ..Must have an agent's picture on the DL..
Address:
27 / 486Brindle rd, Marsden VIC 3047
Ph:03 9412 7306
email:info@kovalinrealestate.com.au
www.kovalinrealestate.com.au
Something like as attached picture..
Target Market(s)
Home Buyers
Industry/Entity Type
Real Estate Agent
Requirements
Must have
- Our Logo Colours

```html
<!DOCTYPE html>
<html lang="en">
<head>
<meta charset="utf-8">
<title>Kovalin Real Estate – New Year Flyer</title>
<link rel="stylesheet" href="https://fonts.googleapis.com/css2?family=Lato:wght@300;400;700&family=Open+Sans:wght@600;700&display=swap">
<style>
  :root{
    --navy:#0c2763;
    --navy-deep:#081c4a;
    --maroon:#7a1520;
    --grey-arc:#d3d5d9;
    --page:#e8e9eb;
    --white:#ffffff;
    --photo-sky:#9fb6cc;
    --photo-suit:#2a3a5c;
    --photo-skin:#c89478;
    --photo-red:#d9534f;
  }
  *{margin:0;padding:0;box-sizing:border-box}
  html,body{width:1196px;height:1200px;overflow:hidden}
  body{background:var(--white);font-family:"Lato",sans-serif;color:var(--white);position:relative}
  .sheet{position:absolute;left:8px;top:8px;width:1180px;height:1184px;background:var(--page)}
  .flyer{position:absolute;left:66px;width:1065px;height:506px;overflow:hidden;box-shadow:0 6px 14px rgba(0,0,0,.18)}
  .flyer--front{top:45px}
  .flyer--back{top:629px}
  .flyer svg{position:absolute;inset:0}
  .layer{position:absolute}
  .brand{display:flex;align-items:center;justify-content:center;gap:12px;font-family:"Lato",sans-serif;font-weight:400;font-size:40px;letter-spacing:3px;color:var(--white);text-transform:uppercase;white-space:nowrap}
  .brand__mark{width:14px;height:14px;background:var(--white)}
  .front-brand{left:40px;width:500px;top:150px}
  .headline{left:40px;width:500px;top:230px;text-align:center;font-weight:300;font-size:38px;line-height:48px}
  .subline{left:20px;width:540px;top:356px;text-align:center;font-size:17px;font-weight:400;letter-spacing:.2px;text-transform:uppercase}
  .subline strong{font-weight:700}
  .cta{left:93px;top:408px;width:400px;height:52px;border-radius:26px;background:var(--white);box-shadow:0 3px 6px rgba(0,0,0,.35);display:flex;align-items:center;justify-content:center;gap:10px;font-family:"Open Sans",sans-serif;font-weight:700;font-size:23px;color:var(--maroon)}
  .cta svg{position:static}
  .cta-note{left:93px;width:400px;top:468px;text-align:center;font-size:19px;font-weight:400}
  .back-brand{left:520px;width:506px;top:118px}
  .contact{left:609px;top:240px;list-style:none}
  .contact__name{font-size:23px;font-weight:400;margin-bottom:22px}
  .contact__item{display:flex;align-items:center;gap:12px;font-size:19px;font-weight:400;height:38px}
  .contact__item svg{position:static;flex:none}
  .address{left:540px;width:520px;top:454px;font-size:20px;font-weight:400;text-align:center}
</style>
</head>
<body>
<div class="sheet"></div>

<section class="flyer flyer--front">
  <svg width="1065" height="506" viewBox="0 0 1065 506">
    <defs>
      <linearGradient id="agentPhoto" x1="0" y1="0" x2="0" y2="1">
        <stop offset="0" stop-color="var(--photo-sky)"/>
        <stop offset=".45" stop-color="#b9b7b0"/>
        <stop offset=".55" stop-color="var(--photo-suit)"/>
        <stop offset="1" stop-color="#1d2a45"/>
      </linearGradient>
      <linearGradient id="navyFront" x1="0" y1="0" x2="1" y2="1">
        <stop offset="0" stop-color="var(--navy)"/>
        <stop offset="1" stop-color="var(--navy-deep)"/>
      </linearGradient>
      <clipPath id="frontPanel"><path d="M0 0 H712 C620 130 598 380 650 506 H0 Z"/></clipPath>
    </defs>
    <rect x="600" y="0" width="465" height="506" fill="url(#agentPhoto)" role="img" aria-label="Photo of the sales agent in a suit standing in front of a large family home"/>
    <path d="M640 0 H790 C712 110 690 300 720 506 H660 C620 360 640 130 720 0 Z" fill="var(--grey-arc)"/>
    <path d="M0 0 H712 C620 130 598 380 650 506 H0 Z" fill="var(--white)" transform="translate(8 0)"/>
    <g clip-path="url(#frontPanel)">
      <rect width="1065" height="506" fill="url(#navyFront)"/>
      <rect x="0" y="432" width="1065" height="74" fill="var(--maroon)"/>
    </g>
  </svg>
  <div class="layer brand front-brand"><span class="brand__mark"></span>Kovalin Real Estate</div>
  <p class="layer headline">Curious to know what your<br>home is worth?</p>
  <p class="layer subline">Start the new year with <strong>Dev Malhotra</strong> and find out!</p>
  <div class="layer cta">CALL ME NOW!
    <svg width="24" height="24" viewBox="0 0 24 24"><circle cx="12" cy="12" r="10" fill="none" stroke="var(--maroon)" stroke-width="2"/><path d="M8.5 7.5c.6-.6 1.3-.4 1.6.2l.8 1.6c.2.5 0 .9-.4 1.2l-.5.4c.5 1.2 1.4 2.1 2.6 2.6l.4-.5c.3-.4.8-.6 1.2-.4l1.6.8c.6.3.8 1 .2 1.6-.8.9-2 1.1-3.2.5-1.9-.9-3.6-2.6-4.5-4.5-.6-1.2-.4-2.4.5-3.2z" fill="var(--maroon)"/></svg>
    0431 782 209</div>
  <p class="layer cta-note">For Free property Appraisal</p>
</section>

<section class="flyer flyer--back">
  <svg width="1065" height="506" viewBox="0 0 1065 506">
    <defs>
      <linearGradient id="housePhoto" x1="0" y1="0" x2="1" y2="1">
        <stop offset="0" stop-color="var(--photo-skin)"/>
        <stop offset=".45" stop-color="var(--photo-red)"/>
        <stop offset="1" stop-color="var(--photo-suit)"/>
      </linearGradient>
      <linearGradient id="navyBack" x1="0" y1="0" x2="1" y2="1">
        <stop offset="0" stop-color="var(--navy)"/>
        <stop offset="1" stop-color="var(--navy-deep)"/>
      </linearGradient>
      <clipPath id="backPanel"><path d="M330 0 C420 100 450 330 420 506 H1065 V0 Z"/></clipPath>
    </defs>
    <rect x="0" y="0" width="520" height="506" fill="url(#housePhoto)" role="img" aria-label="Photo of two hands sheltering a small red model house"/>
    <path d="M240 0 H330 C420 100 450 330 420 506 H405 C430 330 380 110 240 0 Z" fill="var(--grey-arc)"/>
    <path d="M330 0 C420 100 450 330 420 506 H1065 V0 Z" fill="var(--white)" transform="translate(-8 0)"/>
    <g clip-path="url(#backPanel)">
      <rect width="1065" height="506" fill="url(#navyBack)"/>
      <rect x="0" y="434" width="1065" height="72" fill="var(--maroon)"/>
    </g>
  </svg>
  <div class="layer brand back-brand"><span class="brand__mark"></span>Kovalin Real Estate</div>
  <ul class="layer contact">
    <li class="contact__name">Dev Malhotra, Sales Manager</li>
    <li class="contact__item">
      <svg width="20" height="20" viewBox="0 0 24 24"><circle cx="12" cy="12" r="10" fill="none" stroke="var(--white)" stroke-width="2"/><path d="M8.5 7.5c.6-.6 1.3-.4 1.6.2l.8 1.6c.2.5 0 .9-.4 1.2l-.5.4c.5 1.2 1.4 2.1 2.6 2.6l.4-.5c.3-.4.8-.6 1.2-.4l1.6.8c.6.3.8 1 .2 1.6-.8.9-2 1.1-3.2.5-1.9-.9-3.6-2.6-4.5-4.5-.6-1.2-.4-2.4.5-3.2z" fill="var(--white)"/></svg>
      03 9412 7306</li>
    <li class="contact__item">
      <svg width="20" height="20" viewBox="0 0 24 24"><circle cx="12" cy="12" r="10" fill="var(--white)"/><rect x="6.5" y="8" width="11" height="8" fill="var(--navy)"/><path d="M6.5 8 L12 12.5 L17.5 8" fill="none" stroke="var(--white)" stroke-width="1.3"/></svg>
      dev.malhotra@kovalinrealestate.com.au</li>
    <li class="contact__item">
      <svg width="20" height="20" viewBox="0 0 24 24" fill="none" stroke="var(--white)" stroke-width="1.6"><circle cx="12" cy="12" r="10"/><ellipse cx="12" cy="12" rx="4" ry="10"/><path d="M2 12 H22 M4 7 H20 M4 17 H20"/></svg>
      www.kovalinrealestate.com.au</li>
  </ul>
  <p class="layer address">27/486 Brindle Rd Marsden, Victoria, Australia 3047</p>
</section>
</body>
</html>
```